Vellisant - Quality health delivered at your door

Vellisant offers home and Community Based Services for adults who wish to continue live independently in their communities. We increase accessibility to health care, reduce health care delivery gap, reduce mortality and morbidity, reduce health while promoting healthy living in the comfort of our patients communities or homes.

We provide on site services and deliver high quality healthcare at your door. Our experienced physicians coordinate care with our certified nurse practitioners and provide chronic care management, physical therapy, rehabilitation and medications management.

Target Market(s)

Older population living in independent living facilities

Industry/Entity Type

Health Care

Contact Information for Business Card

Vellisant

Number of Pages Required

4 page

Font styles to use
Sans Serif

Colors

Designer to choose colors to be used in the design.

```html
<!DOCTYPE html>
<html lang="en">
<head>
<meta charset="utf-8">
<title>Vellisant</title>
<link href="https://fonts.googleapis.com/css2?family=Cinzel:wght@400;700&family=Noto+Sans:wght@400;600&family=Montserrat:ital,wght@1,400&display=swap" rel="stylesheet">
<style>
:root{
  --green:#4d6a17;
  --green-dark:#223a05;
  --green-text:#1f3307;
  --orange:#f4971b;
  --olive:#7a9a2e;
  --ink:#333;
  --muted:#555;
  --white:#fff;
}
*{margin:0;padding:0;box-sizing:border-box}
html,body{width:906px;height:1200px;overflow:hidden;background:var(--white)}
body{position:relative;font-family:"Noto Sans",sans-serif;color:var(--ink)}
.abs{position:absolute}
.serif{font-family:"Cinzel",serif}

.brand{left:58px;top:8px;width:115px;text-align:center}
.brand-mark{width:58px;height:58px;border-radius:50%;background:var(--orange);border:3px solid var(--green-dark);margin:0 auto}
.brand-name{font-size:16px;color:var(--green-dark);margin-top:4px;letter-spacing:.5px}

.mail-icon{left:506px;top:30px}
.mail-label{left:559px;top:28px;font-size:14px;color:var(--olive)}
.mail-addr{left:559px;top:50px;font-size:13px;color:var(--muted)}

.btn{background:linear-gradient(var(--green),var(--green-dark));color:var(--white);font-family:"Cinzel",serif;font-size:15px;letter-spacing:1px;display:flex;align-items:center;justify-content:center;border:1px solid #2c4507}
.btn-head{left:714px;top:24px;width:134px;height:46px}

.nav{left:0;top:94px;width:906px;height:47px;background:linear-gradient(var(--green),var(--green-dark));display:flex;padding-left:55px}
.nav a{color:var(--white);font-size:11.5px;text-decoration:none;line-height:47px;padding:0 8.5px}
.nav a.active{background:var(--orange);padding:0 11px}

.hero-photo{left:0;top:141px;width:906px;height:369px;background:linear-gradient(90deg,#9a8878 0%,#c9c3bf 25%,#e9ecef 45%,#f3f5f7 70%,#e4e8ea 100%)}
.hero-title{left:462px;top:236px;font-size:50px;font-weight:700;color:#111;letter-spacing:1px}
.hero-text{left:464px;top:302px;width:370px;font-family:"Montserrat",sans-serif;font-style:italic;font-size:13.5px;line-height:20px;color:#333}
.btn-hero{left:461px;top:359px;width:134px;height:47px}
.dot{width:10px;height:10px;border-radius:50%;background:var(--orange);left:874px}

.card-panel{left:58px;top:470px;width:790px;height:160px;background:var(--white)}
.card{top:477px;width:244px;height:141px;padding:22px 14px 0 18px;color:var(--white)}
.card h3{font-family:"Cinzel",serif;font-size:15px;line-height:17px;font-weight:400;letter-spacing:.5px}
.card p{font-size:11px;line-height:17.5px;margin-top:11px}
.c1{left:64px;background:linear-gradient(135deg,#6d7044,#47512a)}
.c2{left:331px;background:linear-gradient(135deg,#6a6a45,#3f4d24)}
.c3{left:599px;background:linear-gradient(135deg,#757150,#4a5530)}
.arrow{top:633px;width:31px;height:23px;border:1.5px solid #222;background:var(--white);display:flex;align-items:center;justify-content:center}

.divider{left:70px;top:705px;width:756px;height:3px;background:radial-gradient(ellipse at center,#777 0%,#bbb 60%,transparent 100%)}
.section-title{left:0;top:728px;width:906px;text-align:center;font-size:30px;color:var(--green-text);font-weight:400;letter-spacing:1px}
.section-text{left:108px;width:690px;text-align:center;font-size:11.2px;line-height:17.5px;color:var(--muted)}

.footer{left:0;top:902px;width:906px;height:251px;background:linear-gradient(#4f6c18,#233b05)}
.f-head{font-family:"Cinzel",serif;font-size:16px;color:var(--white);letter-spacing:1px}
.f-text{font-size:11px;color:var(--white)}
.news-date{font-size:9px;color:#d9dcc8;display:flex;align-items:center;gap:5px}
.cal{width:10px;height:10px;border:1.5px solid var(--orange);border-top-width:3px}
.f-input{left:282px;top:994px;width:189px;height:40px;background:var(--white);border:1px solid #ccc;font-size:11px;color:#999;padding:12px 10px}
.f-btn{left:282px;top:1039px;width:118px;height:33px;background:var(--white);font-family:"Cinzel",serif;font-size:13px;letter-spacing:1px;color:var(--green-text);display:flex;align-items:center;justify-content:center}
.social{top:1088px;width:23px;height:23px;border:1px solid #b9c3a4}
.social.on{background:var(--white)}
.bottom{left:0;top:1153px;width:906px;height:47px;background:var(--orange);display:flex;align-items:center;justify-content:center;font-size:11px;color:#333;gap:4px}
.bottom .serif{font-size:15px;color:var(--white)}
</style>
</head>
<body>

<header>
  <div class="abs brand">
    <div class="brand-mark"></div>
    <div class="brand-name">Vellisant</div>
  </div>
  <svg class="abs mail-icon" width="44" height="35" viewBox="0 0 44 35" aria-hidden="true">
    <rect x="0" y="0" width="44" height="35" rx="4" fill="#f4971b"/>
    <path d="M2 4 L22 20 L42 4" fill="none" stroke="#fff" stroke-width="3"/>
  </svg>
  <div class="abs mail-label">Email :</div>
  <div class="abs mail-addr">info@vellisant.com</div>
  <div class="abs btn btn-head">CONTACT US</div>
</header>

<nav class="abs nav">
  <a class="active">Home</a><a>Assisted Living</a><a>Skilled Nursing</a><a>Independent Living</a><a>Services</a><a>Respite Care</a><a>Rehabilitation</a><a>Kinrei Learning Center</a><a>Kinrei</a>
</nav>

<section>
  <div class="abs hero-photo" role="img" aria-label="Photo of a smiling older couple embracing outdoors with misty mountains behind"></div>
  <h1 class="abs hero-title serif">VELLISANT</h1>
  <p class="abs hero-text">Lorem Ipsum is simply dummy text of the printing and typesetting industry. Lorem Ipsum has been the industry's.</p>
  <div class="abs btn btn-hero">CONTACT US</div>
  <div class="abs dot" style="top:290px;background:var(--olive)"></div>
  <div class="abs dot" style="top:308px"></div>
  <div class="abs dot" style="top:327px"></div>
  <div class="abs dot" style="top:348px"></div>

  <div class="abs card-panel"></div>
  <div class="abs card c1" role="img" aria-label="Photo of a caregiver helping an older adult at home"><h3>Comprehensive primary care services</h3><p>Lorem Ipsum is simply dummy text of the printing and type industry.</p></div>
  <div class="abs card c2" role="img" aria-label="Photo of a nurse with an older adult in a wheelchair outdoors"><h3>Coordination of speciality care</h3><p>Lorem Ipsum is simply dummy text of the printing and type industry.</p></div>
  <div class="abs card c3" role="img" aria-label="Photo of a doctor reviewing notes with an older patient"><h3>Asthma, diabetes mellitus, heart</h3><p>Lorem Ipsum is simply dummy text of the printing and type industry.</p></div>

  <div class="abs arrow" style="left:419px"><svg width="14" height="10" viewBox="0 0 14 10"><path d="M0 5 L6 0 V3 H14 V7 H6 V10 Z" fill="#f4971b"/></svg></div>
  <div class="abs arrow" style="left:456px"><svg width="14" height="10" viewBox="0 0 14 10"><path d="M14 5 L8 0 V3 H0 V7 H8 V10 Z" fill="#111"/></svg></div>
</section>

<section>
  <div class="abs divider"></div>
  <h2 class="abs section-title serif">STAY HOME</h2>
  <p class="abs section-text" style="top:777px">Vellisant offers home and Community Based Services for adults who wish to continue to live independently in the comfort of their communities.</p>
  <p class="abs section-text" style="top:829px">We provide on site services and deliver high quality healthcare at your door. Our experienced physicians coordinate care with our certified nurse practitioners and provide chronic care management, physical therapy, rehabilitation and medications management.</p>
</section>

<footer>
  <div class="abs footer"></div>
  <div class="abs f-head" style="left:60px;top:938px;font-size:14px">Last News</div>
  <div class="abs f-text" style="left:61px;top:974px">Lorem Ipsum is simply dummy text</div>
  <div class="abs news-date" style="left:61px;top:997px"><span class="cal"></span>Today 2:10 pm - 30.05.2017</div>
  <div class="abs f-text" style="left:61px;top:1024px">Lorem Ipsum is simply dummy text</div>
  <div class="abs news-date" style="left:61px;top:1047px"><span class="cal"></span>Today 2:10 pm - 30.05.2017</div>
  <div class="abs f-text" style="left:61px;top:1072px">Lorem Ipsum is simply dummy text</div>
  <div class="abs news-date" style="left:61px;top:1095px"><span class="cal"></span>Today 2:10 pm - 30.05.2017</div>

  <div class="abs f-head" style="left:283px;top:938px">Newsletter</div>
  <div class="abs f-text" style="left:283px;top:970px">Subscribe to Our Newsletter</div>
  <div class="abs f-input">E-Mail</div>
  <div class="abs f-btn">SUBSCRIBE</div>

  <div class="abs f-head" style="left:492px;top:938px">Usefull Link</div>
  <div class="abs f-text" style="left:492px;top:971px">Home</div>
  <div class="abs f-text" style="left:492px;top:995px">About US</div>
  <div class="abs f-text" style="left:492px;top:1018px">Services</div>
  <div class="abs f-text" style="left:492px;top:1042px">Blogs/News</div>
  <div class="abs f-text" style="left:492px;top:1065px">Contact Us</div>

  <div class="abs f-head" style="left:672px;top:938px">Follow Us</div>
  <div class="abs f-head" style="left:672px;top:968px;font-size:14px">Our Locations</div>
  <div class="abs f-text" style="left:672px;top:991px;line-height:16px;color:#e6e9dc">123, Lorem ipsum dummy text,<br>Country-123456.</div>
  <div class="abs f-head" style="left:672px;top:1038px;font-size:14px">Phone</div>
  <div class="abs f-text" style="left:675px;top:1059px;color:#e6e9dc">+1.123.456.7878</div>
  <div class="abs social on" style="left:670px"></div>
  <div class="abs social" style="left:701px"></div>
  <div class="abs social" style="left:732px"></div>
  <div class="abs social" style="left:763px"></div>
  <div class="abs social" style="left:793px"></div>
  <div class="abs social" style="left:824px"></div>

  <div class="abs bottom">© <span class="serif">VELLISANT</span> - 2017. All rights reserved.</div>
</footer>

</body>
</html>
```